Business card for medical clinic

I need an upmarket, modern medical/health business card for my clinic

Contact Information for Business Card

name, address, email, qr code

```html
<!DOCTYPE html>
<html lang="en">
<head>
<meta charset="utf-8">
<title>Meridian Care Partners – Business Card</title>
<link rel="stylesheet" href="https://fonts.googleapis.com/css2?family=Cinzel:wght@500;600&family=Crimson+Text:wght@400&display=swap">
<style>
  :root {
    --page-bg: #e6e3df;
    --card-bg: #f3f5f6;
    --card-edge: #d9dde0;
    --brand-blue: #1d5a86;
    --name-blue: #1f4f7a;
    --text-grey: #4a4f55;
    --icon-blue: #1e5f8c;
    --accent-navy: #1f3a68;
    --accent-teal: #1f93b3;
  }
  * { margin: 0; padding: 0; box-sizing: border-box; }
  html, body {
    width: 1200px;
    height: 1054px;
    overflow: hidden;
    background: var(--page-bg);
  }
  .canvas {
    position: relative;
    width: 1200px;
    height: 1054px;
  }
  .card {
    position: absolute;
    left: 60px;
    top: 202px;
    width: 1080px;
    height: 650px;
    background: var(--card-bg);
    border: 1px solid var(--card-edge);
    border-radius: 26px;
    box-shadow: 0 10px 30px rgba(0,0,0,0.08);
    overflow: hidden;
  }
  .accent-disc {
    position: absolute;
    left: 476px;
    top: 28px;
    width: 600px;
    height: 600px;
  }
  .brand {
    position: absolute;
    left: 38px;
    top: 62px;
    display: flex;
    align-items: center;
    gap: 18px;
  }
  .brand-dot {
    width: 64px;
    height: 64px;
    border-radius: 50%;
    background: var(--brand-blue);
  }
  .brand-name {
    font-family: "Cinzel", serif;
    font-weight: 600;
    color: var(--brand-blue);
    font-size: 34px;
    line-height: 1.05;
    letter-spacing: 0.5px;
  }
  .brand-name span { display: block; font-size: 20px; letter-spacing: 5px; }
  .person {
    position: absolute;
    left: 50px;
    top: 305px;
  }
  .person-name {
    font-family: "Cinzel", serif;
    font-weight: 600;
    font-size: 38px;
    color: var(--name-blue);
    letter-spacing: 1px;
  }
  .person-title {
    font-family: "Crimson Text", serif;
    font-weight: 400;
    font-size: 27px;
    color: var(--text-grey);
    margin-top: -2px;
  }
  .contacts {
    position: absolute;
    left: 50px;
    top: 432px;
    list-style: none;
    font-family: "Crimson Text", serif;
    font-size: 26px;
    color: var(--text-grey);
  }
  .contacts li {
    display: flex;
    align-items: center;
    height: 39px;
    white-space: nowrap;
  }
  .contacts svg {
    width: 22px;
    height: 22px;
    margin-right: 18px;
    fill: var(--icon-blue);
  }
  .address {
    position: absolute;
    left: 50px;
    top: 562px;
    font-family: "Crimson Text", serif;
    font-size: 28px;
    color: var(--text-grey);
    white-space: nowrap;
  }
</style>
</head>
<body>
<div class="canvas">
  <section class="card">
    <svg class="accent-disc" viewBox="0 0 600 600" role="img" aria-label="Brand accent area in navy-to-teal tones">
      <defs>
        <linearGradient id="accentFade" x1="0" y1="0" x2="0" y2="1">
          <stop offset="0" stop-color="var(--accent-navy)"/>
          <stop offset="1" stop-color="var(--accent-teal)"/>
        </linearGradient>
      </defs>
      <circle cx="300" cy="300" r="290" fill="url(#accentFade)" opacity="0.22"/>
    </svg>

    <div class="brand">
      <div class="brand-dot"></div>
      <div class="brand-name">Meridian Care<span>Partners</span></div>
    </div>

    <div class="person">
      <h1 class="person-name">DANIEL HALE</h1>
      <p class="person-title">Managing Director</p>
    </div>

    <ul class="contacts">
      <li>
        <svg viewBox="0 0 24 24" aria-hidden="true"><path d="M6.6 10.8a15.1 15.1 0 0 0 6.6 6.6l2.2-2.2a1 1 0 0 1 1-.25 11.4 11.4 0 0 0 3.6.57 1 1 0 0 1 1 1V20a1 1 0 0 1-1 1A17 17 0 0 1 3 4a1 1 0 0 1 1-1h3.5a1 1 0 0 1 1 1c0 1.25.2 2.45.57 3.57a1 1 0 0 1-.25 1z"/></svg>
        0755-312-48190
      </li>
      <li>
        <svg viewBox="0 0 24 24" aria-hidden="true"><path d="M2 5h20v14H2z M4 7v.4l8 5.2 8-5.2V7z" fill-rule="evenodd"/></svg>
        hello@meridiancare.com
      </li>
      <li>
        <svg viewBox="0 0 24 24" aria-hidden="true"><path d="M12 2a10 10 0 1 0 0 20 10 10 0 0 0 0-20zm6.9 6h-2.9a15.6 15.6 0 0 0-1.4-3.6A8 8 0 0 1 18.9 8zM12 4a14 14 0 0 1 1.9 4h-3.8A14 14 0 0 1 12 4zM4.3 14a8 8 0 0 1 0-4h3.4a16 16 0 0 0 0 4zm.8 2h2.9a15.6 15.6 0 0 0 1.4 3.6A8 8 0 0 1 5.1 16zM8 8H5.1a8 8 0 0 1 4.3-3.6A15.6 15.6 0 0 0 8 8zm4 12a14 14 0 0 1-1.9-4h3.8A14 14 0 0 1 12 20zm2.3-6H9.7a14.7 14.7 0 0 1 0-4h4.6a14.7 14.7 0 0 1 0 4zm.3 5.6A15.6 15.6 0 0 0 16 16h2.9a8 8 0 0 1-4.3 3.6zM16.3 14a16 16 0 0 0 0-4h3.4a8 8 0 0 1 0 4z"/></svg>
        www.meridiancare.com
      </li>
    </ul>

    <p class="address">118 Harbour Lane, Millbrook, US 48201</p>
  </section>
</div>
</body>
</html>
```